NZ First of it's kind solutions directory and marketplace for busy Mums needs a business card design

We need a business card design for our new nationwide business in NZ (long term plans to go global). We provide solutions to the everyday challenges that busy Mums face by connecting them with quality communities and suppliers of carefully selected, relevant products and services. We sell direct via our online marketplace. The final design should communicate our values of inclusivity, quality and smart solutions. Colours should incorporate our logo colour palette of #477077 and #6ba8b2. Our website is at https://www.brightnestmums.example

Target Market(s)

busy Mums, Age 28 – 50, female, income over $100K, location main centres NZ primarily but NZ wide. Is likely juggling work or career with a young family. Probably had hobbies which have fallen by the wayside.
-Wants to succeed in her chosen career without compromising on family life
-to successfully juggle her career without feeling like she is compromising her children
- Is time poor, something always has to give and it’s generally her health (she’ll stay up late, get stressed)
- probably ex corporate or professional career. Has discretional income

Industry/Entity Type

Business

Contact Information for Business Card

Lena Forbisher, Founder, BrightNestMums.example (Strapline Tap; Gather; Sorted), 47 Kowhai Terrace, Ellerslie, Auckland 1051, New Zealand. Mob: 021 483 517 Ph: +64 (0)9 571 4860

Font styles to use
Other font styles liked:
• Raleway, and/or Architects Daughter

Colors
00a990
33b8a4
86cfc6
cfeae6

Requirements
Must have
• the above details, streamline. the logo and colours associated with those logos
Should not have
• foil or metallic colours

```html
<!DOCTYPE html>
<html lang="en">
<head>
<meta charset="utf-8">
<title>BrightNestMums business card</title>
<link rel="stylesheet" href="https://fonts.googleapis.com/css2?family=Baloo+2:wght@600&family=Roboto:ital,wght@0,400;1,400&display=swap">
<style>
  :root {
    --teal-dark: #3d5f66;
    --teal-light: #5b98a2;
    --ink: #333a3c;
    --card: #f7f7f6;
    --backdrop: #e3e3e3;
  }
  * { margin: 0; padding: 0; box-sizing: border-box; }
  html, body { width: 1200px; height: 576px; overflow: hidden; background: var(--backdrop); }
  .canvas { position: relative; width: 1200px; height: 576px; }
  .card {
    position: absolute; top: 138px; width: 485px; height: 294px;
    background: var(--card); border-radius: 13px; overflow: hidden;
    box-shadow: 0 2px 5px rgba(0,0,0,0.18);
  }
  .card--front { left: 82px; }
  .card--back { left: 602px; width: 480px; }

  .front-disc {
    position: absolute; left: 12px; top: 130px; width: 152px; height: 152px;
    border-radius: 50%; background: var(--teal-dark);
  }
  .wordmark {
    font-family: "Baloo 2", sans-serif; font-weight: 600; color: var(--teal-dark);
    line-height: 1; white-space: nowrap;
  }
  .strapline {
    font-family: "Roboto", sans-serif; font-size: 11px; color: var(--ink);
    letter-spacing: 4px; text-transform: uppercase; white-space: nowrap;
  }
  .strapline .sep { color: var(--teal-light); padding: 0 6px; letter-spacing: 0; }
  .front-lockup { position: absolute; right: 30px; top: 196px; text-align: right; }
  .front-lockup .wordmark { font-size: 36px; }
  .front-lockup .strapline { margin-top: 6px; margin-right: -4px; }

  .back-lockup { position: absolute; left: 34px; top: 84px; width: 200px; text-align: center; }
  .back-lockup .dot {
    width: 36px; height: 36px; border-radius: 50%; background: var(--teal-dark);
    margin: 0 auto 30px;
  }
  .back-lockup .wordmark { font-size: 25px; }
  .back-lockup .strapline { font-size: 9px; letter-spacing: 3px; margin-top: 4px; }

  .details { position: absolute; left: 268px; top: 50px; font-family: "Roboto", sans-serif; color: var(--ink); }
  .details .name { font-family: "Baloo 2", sans-serif; font-weight: 600; font-size: 22px; color: var(--teal-dark); line-height: 1; }
  .details .role { font-style: italic; font-size: 12.5px; margin-top: 2px; }
  .details .address { font-size: 12.5px; line-height: 18px; margin-top: 16px; }
  .contact { list-style: none; margin-top: 10px; font-size: 12.5px; }
  .contact li { display: flex; align-items: center; height: 18px; }
  .contact svg { width: 12px; height: 12px; margin-right: 9px; fill: var(--teal-dark); }

  .footer-band { position: absolute; left: 0; bottom: 0; width: 480px; height: 38px; }
  .web {
    position: absolute; left: 268px; bottom: 14px;
    font-family: "Roboto", sans-serif; font-size: 12.5px; color: #fff;
  }
</style>
</head>
<body>
<main class="canvas">
  <section class="card card--front">
    <div class="front-disc"></div>
    <div class="front-lockup">
      <div class="wordmark">BrightNestMums</div>
      <div class="strapline">Tap<span class="sep">|</span>Gather<span class="sep">|</span>Sorted</div>
    </div>
  </section>

  <section class="card card--back">
    <div class="back-lockup">
      <div class="dot"></div>
      <div class="wordmark">BrightNestMums</div>
      <div class="strapline">Tap<span class="sep">|</span>Gather<span class="sep">|</span>Sorted</div>
    </div>

    <div class="details">
      <div class="name">Lena Forbisher</div>
      <div class="role">Founder</div>
      <div class="address">47 Kowhai Terrace, Ellerslie,<br>Auckland 1051, New Zealand</div>
      <ul class="contact">
        <li><svg viewBox="0 0 12 12"><rect x="3" y="0.5" width="6" height="11" rx="1.2"/><rect x="4" y="2" width="4" height="6.5" fill="#f7f7f6"/></svg>021 483 517</li>
        <li><svg viewBox="0 0 12 12"><path d="M1 4c0-2 2-3 5-3s5 1 5 3v1H8V3.5H4V5H1z"/><rect x="2" y="6" width="8" height="5" rx="1"/></svg>+64 (0)9 571 4860</li>
        <li><svg viewBox="0 0 12 12"><path d="M0.5 2.5h11v7h-11z"/><path d="M0.5 2.5L6 7l5.5-4.5" fill="none" stroke="#f7f7f6" stroke-width="1"/></svg>lena@brightnestmums.example</li>
      </ul>
    </div>

    <svg class="footer-band" viewBox="0 0 480 38" aria-hidden="true">
      <rect x="0" y="24" width="480" height="14" fill="var(--teal-light)"/>
      <path d="M236 0H480V38H218L230 6Q232 0 236 0Z" fill="var(--teal-dark)"/>
    </svg>
    <div class="web">www.BrightNestMums.example</div>
  </section>
</main>
</body>
</html>
```